National Intensive Course Provider needs an advert designed to appear in trams

We need an advertisement designed to put in trams, the dimensions are 660mm wide and 203mm height. We offer intensive driving courses all over the UK, allowing pupils to complete a full driving course within a week/two weeks with both the theory and practical tests included in the course (as required). We would like the colours used to be green and dark blue, maybe red also, whatever looks best from them colours really.

Key Points to highlight:
- Pass your driving test within 1 week
- Start your course as early as next week
- Both tests included as part of your course (if required)

I have attached some images which could be included in the design

```html
<!DOCTYPE html>
<html lang="en">
<head>
<meta charset="utf-8">
<title>Kestrel Intensive Driving Courses – Tram Advert</title>
<link rel="stylesheet" href="https://fonts.googleapis.com/css2?family=Roboto:wght@400;500;700;900&display=swap">
<style>
  :root {
    --navy: #0b0f3f;
    --red: #e3061a;
    --silver-light: #f4f4f4;
    --silver-dark: #a3a6aa;
    --white: #ffffff;
    --stage: #e4e5e6;
    --photo-sky: #d3e2ea;
    --photo-denim: #9db4cf;
    --photo-car: #1f56c4;
    --photo-car-deep: #0d2d86;
    --photo-trees: #4f7d3a;
    --photo-trees-light: #97b872;
    --photo-redcar: #c4232b;
  }
  * { margin: 0; padding: 0; box-sizing: border-box; }
  html, body {
    width: 1200px;
    height: 514px;
    overflow: hidden;
    background: var(--stage);
    font-family: "Roboto", Arial, sans-serif;
  }
  .advert {
    position: absolute;
    left: 66px;
    top: 96px;
    width: 1070px;
    height: 330px;
    overflow: hidden;
    box-shadow: 0 6px 14px rgba(0,0,0,0.25);
  }
  .advert-shapes {
    position: absolute;
    inset: 0;
    width: 100%;
    height: 100%;
    display: block;
  }

  /* Brand */
  .brand {
    position: absolute;
    left: 521px;
    top: 30px;
    width: 200px;
    text-align: center;
    color: var(--white);
  }
  .brand-name {
    display: block;
    font-weight: 900;
    font-size: 40px;
    line-height: 40px;
    letter-spacing: 1px;
  }
  .brand-tagline {
    display: block;
    margin-top: 14px;
    font-weight: 400;
    font-size: 13.5px;
    line-height: 20px;
    letter-spacing: 2px;
  }

  /* Headline */
  .headline-line {
    position: absolute;
    right: 35px;
    white-space: nowrap;
    text-align: right;
    font-weight: 700;
  }
  .headline-main { color: var(--white); font-size: 44px; line-height: 44px; letter-spacing: -0.5px; }
  .headline-main.we-offer { top: 28px; }
  .headline-main.all-over { top: 133px; font-size: 41px; line-height: 41px; }
  .headline-sub { color: var(--red); font-size: 30px; line-height: 30px; letter-spacing: -0.3px; }
  .headline-sub.line-one { top: 72px; }
  .headline-sub.line-two { top: 100px; }
  .headline-accent { color: var(--red); }

  /* Benefits */
  .benefits {
    position: absolute;
    right: 35px;
    top: 195px;
    list-style: none;
    color: var(--white);
    font-weight: 500;
    font-size: 18.5px;
    line-height: 24px;
  }
  .benefit {
    display: flex;
    justify-content: flex-end;
    align-items: flex-start;
    gap: 10px;
    text-align: right;
    margin-bottom: 7px;
    white-space: nowrap;
  }
  .benefit-tick {
    flex: none;
    width: 17px;
    height: 24px;
  }
  .benefit-tick path {
    fill: none;
    stroke: var(--red);
    stroke-width: 2.6;
    stroke-linecap: round;
    stroke-linejoin: round;
  }
</style>
</head>
<body>
<section class="advert" aria-label="Kestrel intensive driving courses advert">
  <svg class="advert-shapes" viewBox="0 0 1250 385" preserveAspectRatio="none" xmlns="http://www.w3.org/2000/svg">
    <defs>
      <linearGradient id="hero-tones" x1="0" y1="0" x2="1" y2="1">
        <stop offset="0" stop-color="var(--photo-sky)"/>
        <stop offset="0.22" stop-color="var(--photo-car)"/>
        <stop offset="0.45" stop-color="var(--photo-denim)"/>
        <stop offset="0.7" stop-color="var(--photo-car)"/>
        <stop offset="1" stop-color="var(--photo-car-deep)"/>
      </linearGradient>
      <linearGradient id="pupil-tones" x1="0" y1="0" x2="0" y2="1">
        <stop offset="0" stop-color="var(--photo-trees-light)"/>
        <stop offset="0.55" stop-color="var(--photo-trees)"/>
        <stop offset="1" stop-color="var(--photo-redcar)"/>
      </linearGradient>
      <linearGradient id="silver" x1="0" y1="0" x2="1" y2="1">
        <stop offset="0" stop-color="var(--silver-light)"/>
        <stop offset="1" stop-color="var(--silver-dark)"/>
      </linearGradient>
    </defs>

    <rect class="hero-photo" x="0" y="0" width="830" height="385" fill="url(#hero-tones)"
          role="img" aria-label="Photo: smiling young driver giving a thumbs up and holding car keys out of a blue car window"/>

    <path class="band-red" d="M470 0 L528 0 C555 150 640 300 800 385 L770 385 C645 300 515 170 470 0 Z" fill="var(--red)"/>
    <path class="band-silver" d="M528 0 L552 0 C582 150 660 300 822 385 L800 385 C640 300 555 150 528 0 Z" fill="url(#silver)"/>
    <path class="panel-navy" d="M552 0 L1250 0 L1250 385 L822 385 C660 300 582 150 552 0 Z" fill="var(--navy)"/>

    <circle class="pupil-ring" cx="623" cy="270" r="102" fill="url(#silver)"/>
    <circle class="pupil-photo" cx="623" cy="270" r="92" fill="url(#pupil-tones)"
            role="img" aria-label="Photo: pupil holding a pass certificate beside a red car"/>
  </svg>

  <div class="brand">
    <span class="brand-name">KESTREL</span>
    <span class="brand-tagline">INTENSIVE DRIVING<br>COURSES</span>
  </div>

  <h1 class="headline">
    <span class="headline-line headline-main we-offer">WE OFFER</span>
    <span class="headline-line headline-sub line-one">INTENSIVE DRIVING</span>
    <span class="headline-line headline-sub line-two">COURSES</span>
    <span class="headline-line headline-main all-over">ALL OVER THE <span class="headline-accent">UK</span></span>
  </h1>

  <ul class="benefits">
    <li class="benefit">
      <svg class="benefit-tick" viewBox="0 0 17 24" aria-hidden="true"><path d="M2 13 l4.5 5 l9 -12"/></svg>
      <span>Pass your driving test within 1 week</span>
    </li>
    <li class="benefit">
      <svg class="benefit-tick" viewBox="0 0 17 24" aria-hidden="true"><path d="M2 13 l4.5 5 l9 -12"/></svg>
      <span>Start your course as early as next week</span>
    </li>
    <li class="benefit">
      <svg class="benefit-tick" viewBox="0 0 17 24" aria-hidden="true"><path d="M2 13 l4.5 5 l9 -12"/></svg>
      <span>Both tests included as part of<br>your course (if required)</span>
    </li>
  </ul>
</section>
</body>
</html>
```